Brand new redesign of Brightpath finance website

I need a new website design that i can advertise a great low interest rate on the front page and capture input application details that will send through to my email address.

some car finance companies will be similar to this would be listed below

tallowcredit.example.com.au
mirabelfinance.example.com.au
finance725.example.com.au
quenbyfinance.example.com.au
finance91.example.com.au

Reason: I have changed the project to a committed project. all the webpages should have the same format just different content and i want to be able to edit the front page easily to update my interest rates.

Target Market(s)

Australian Finance market targeting a younger demographic

Industry/Entity Type

Finance

Coding

Coded - Design and coding required

Number of Pages Required

5+ page

Font styles to use
Serif
Sans Serif

Colors
0255a3
ffffff
cedeed

Requirements
Must have
• application capture form
• apply now buttons
• Headline rate front page

```html
<!DOCTYPE html>
<html lang="en">
<head>
<meta charset="utf-8">
<title>Brightpath Finance</title>
<link href="https://fonts.googleapis.com/css2?family=Roboto:wght@300;400;500;700&family=Roboto+Condensed:wght@400;700&family=Open+Sans:ital,wght@0,400;0,600;1,400&display=swap" rel="stylesheet">
<style>
:root{
  --blue:#0255a3;
  --blue-deep:#0a4d95;
  --blue-mid:#2b6fb6;
  --sky:#cedeed;
  --white:#ffffff;
  --ink:#333333;
  --muted:#666666;
  --soft:#f4f4f4;
  --line:#e2e2e2;
  --dark:#2f2f2f;
  --green:#1f9d55;
  --foot-bar:#8a8a8a;
  --accent:#1a8fd6;
}
*{box-sizing:border-box;margin:0;padding:0}
html,body{width:1200px;height:2609px;overflow:hidden}
body{position:relative;background:var(--white);font-family:"Roboto",Arial,sans-serif;color:var(--ink)}
.abs{position:absolute}

/* header */
.site-header{position:absolute;left:0;top:0;width:1200px;height:125px;background:var(--white);border-bottom:1px solid var(--line)}
.brand{position:absolute;left:99px;top:22px;display:flex;align-items:center;gap:10px}
.brand-dot{width:46px;height:46px;border-radius:50%;background:var(--blue)}
.brand-name{font-family:"Roboto Condensed",sans-serif;font-weight:700;font-size:26px;color:var(--blue);line-height:1;text-transform:uppercase}
.header-phone{position:absolute;left:790px;top:30px;font-size:19px;color:var(--ink);display:flex;align-items:center;gap:10px}
.btn-apply-top{position:absolute;left:979px;top:23px;width:122px;height:36px;background:var(--blue-mid);color:var(--white);font-size:13px;display:flex;align-items:center;justify-content:center;border-radius:2px;text-transform:uppercase}
.main-nav{position:absolute;top:84px;left:0;width:1200px;font-size:12.5px;text-transform:uppercase;color:var(--ink)}
.main-nav span{position:absolute}
.main-nav .active{color:var(--blue)}

/* hero */
.hero{position:absolute;left:0;top:125px;width:1200px;height:578px;overflow:hidden}
.hero-photo{position:absolute;inset:0;background:linear-gradient(90deg,#eef6e6 0%,#f1f5ee 22%,#c9d3da 42%,#8ea2b4 58%,#b7c3cd 75%,#d9dfe3 100%)}
.hero-kicker{position:absolute;left:97px;top:196px;font-family:"Roboto Condensed",sans-serif;font-size:31px;color:var(--blue);text-transform:uppercase}
.hero-title{position:absolute;left:97px;top:233px;font-family:"Roboto Condensed",sans-serif;font-weight:700;font-size:41px;color:var(--dark);text-transform:uppercase}
.hero-copy{position:absolute;left:97px;top:287px;width:360px;font-size:14px;line-height:22px;color:var(--ink)}
.btn-read{position:absolute;left:97px;top:372px;width:126px;height:37px;background:var(--blue);color:var(--white);font-size:13px;display:flex;align-items:center;justify-content:center;border-radius:2px;text-transform:uppercase}
.slide-arrow{position:absolute;top:318px;width:34px;height:34px;border-radius:50%;background:rgba(120,120,120,.55);display:flex;align-items:center;justify-content:center}

.apply-panel{position:absolute;left:788px;top:40px;width:313px;height:492px;background:rgba(2,85,163,.85)}
.apply-panel h2{position:absolute;left:38px;top:30px;font-family:"Roboto Condensed",sans-serif;font-weight:400;font-size:25px;color:var(--white);text-transform:uppercase}
.field{position:absolute;left:31px;width:254px;height:37px;background:var(--white);font-size:11.5px;color:#888;padding-left:12px;display:flex;align-items:center}
.field-select::after{content:"";position:absolute;right:12px;top:16px;border:5px solid transparent;border-top-color:#666}
.btn-signup{position:absolute;left:31px;top:306px;width:254px;height:37px;background:#2b2b2b;color:var(--white);font-size:15px;display:flex;align-items:center;justify-content:center;text-transform:uppercase}
.rates{position:absolute;left:0;top:364px;width:313px;height:128px;background:rgba(70,80,95,.7);padding:30px 0 0 41px;color:var(--white)}
.rates h3{font-weight:500;font-size:13.5px;text-transform:uppercase;margin-bottom:10px}
.rate-row{display:flex;font-size:13.5px;line-height:21px}
.rate-row span:first-child{width:172px}

/* services */
.services{position:absolute;left:0;top:703px;width:1200px;height:558px;background:var(--soft)}
.section-title{position:absolute;left:0;width:1200px;text-align:center;font-size:31px;font-weight:400;text-transform:uppercase;color:var(--dark)}
.title-rule{position:absolute;left:567px;width:66px;height:2px;background:#555}
.service-card{position:absolute;top:142px;width:238px;height:338px;background:var(--white);border:1px solid var(--line)}
.service-head{height:45px;background:var(--blue-deep);color:var(--white);font-size:17px;display:flex;align-items:center;justify-content:center}
.service-photo{height:150px}
.service-text{padding:12px 14px 0;font-size:11.5px;line-height:20px;text-align:center;color:var(--muted)}
.btn-click{position:absolute;left:61px;top:284px;width:116px;height:30px;border:1.5px solid var(--blue-deep);border-radius:15px;font-size:11px;color:var(--dark);display:flex;align-items:center;justify-content:center;gap:7px;text-transform:uppercase}

/* steps */
.steps{position:absolute;left:0;top:1261px;width:1200px;height:548px;background:linear-gradient(180deg,#1c63b0 0%,#0a56a5 100%);color:var(--white)}
.steps-photo{position:absolute;inset:0;background:radial-gradient(ellipse at 30% 85%,rgba(255,255,255,.12),transparent 55%),radial-gradient(ellipse at 80% 30%,rgba(0,30,80,.18),transparent 60%)}
.steps .section-title{color:var(--white)}
.step-circle{position:absolute;top:156px;width:108px;height:108px;border-radius:50%;background:var(--white);display:flex;align-items:center;justify-content:center}
.step-title{position:absolute;top:283px;width:380px;text-align:center;font-size:22px}
.step-text{position:absolute;top:320px;width:270px;text-align:center;font-size:11.5px;line-height:21px}
.btn-apply-steps{position:absolute;left:501px;top:433px;width:198px;height:47px;background:var(--sky);color:var(--blue);font-size:17px;display:flex;align-items:center;justify-content:center;border-radius:2px;text-transform:uppercase}

/* reviews */
.reviews{position:absolute;left:0;top:1809px;width:1200px;height:386px;background:var(--white)}
.review{position:absolute;top:140px;width:460px;border-left:1px solid var(--line);padding-left:28px;height:170px}
.review-text{font-family:"Open Sans",sans-serif;font-style:italic;font-size:14px;line-height:23px;color:var(--muted)}
.review-text::before{content:"\201C";font-size:24px;margin-right:4px;vertical-align:-4px}
.reviewer{position:absolute;top:102px;display:flex;align-items:center;gap:22px}
.avatar{width:74px;height:74px;border-radius:50%;background:radial-gradient(circle at 50% 40%,#d9c4b0,#9a8a7c)}
.reviewer-name{font-family:"Open Sans",sans-serif;font-style:italic;font-size:13px;color:var(--blue)}
.stars{display:flex;gap:2px;margin-top:7px}
.stars span{width:14px;height:14px;background:var(--green);display:flex;align-items:center;justify-content:center}

/* partners */
.partners{position:absolute;left:0;top:2195px;width:1200px;height:104px;background:#f7f7f7;border-top:1px solid var(--line)}
.partner{position:absolute;top:37px;height:32px;background:#c8c8c8;border-radius:3px}

/* footer */
.site-footer{position:absolute;left:0;top:2299px;width:1200px;height:254px;background:linear-gradient(180deg,#eef0f3,#e4e8ec)}
.foot-brand{position:absolute;left:99px;top:80px;display:flex;flex-direction:column;align-items:center;gap:8px}
.foot-col h4{position:absolute;top:36px;font-size:15px;font-weight:400;text-transform:uppercase;color:var(--dark)}
.contact-line{position:absolute;left:276px;font-size:12.5px;line-height:20px;color:var(--ink);display:flex;gap:12px}
.newsletter-copy{position:absolute;left:624px;top:70px;width:280px;font-size:11.5px;line-height:20px;color:var(--ink)}
.news-input{position:absolute;left:624px;width:264px;height:40px;background:var(--white);font-size:11.5px;padding-left:14px;display:flex;align-items:center;color:#555}
.btn-subscribe{position:absolute;left:789px;top:167px;width:99px;height:40px;background:var(--accent);color:var(--white);font-size:12px;display:flex;align-items:center;justify-content:center;text-transform:uppercase}
.info-links{position:absolute;left:970px;top:72px;font-size:11.5px;line-height:26.5px;color:var(--ink);list-style:none}
.footer-bar{position:absolute;left:0;top:2553px;width:1200px;height:56px;background:var(--foot-bar);color:var(--white);font-size:12px;display:flex;align-items:center;justify-content:center;text-transform:uppercase}
</style>
</head>
<body>

<header class="site-header">
  <div class="brand"><span class="brand-dot"></span><span class="brand-name">Brightpath Finance</span></div>
  <div class="header-phone">
    <svg width="18" height="18" viewBox="0 0 24 24"><path fill="#0255a3" d="M6.6 10.8a15.1 15.1 0 0 0 6.6 6.6l2.2-2.2c.3-.3.7-.4 1-.2 1.1.4 2.3.6 3.6.6.6 0 1 .4 1 1V20c0 .6-.4 1-1 1A17 17 0 0 1 3 4c0-.6.4-1 1-1h3.5c.6 0 1 .4 1 1 0 1.3.2 2.5.6 3.6.1.3 0 .7-.2 1z"/></svg>
    +1300 555 017
  </div>
  <div class="btn-apply-top">Apply Now</div>
  <nav class="main-nav">
    <span class="active" style="left:529px">Home</span>
    <span style="left:607px">About Brightpath</span>
    <span style="left:755px">Our Services</span>
    <span style="left:882px">Privacy Policy</span>
    <span style="left:1023px">Contact Us</span>
  </nav>
</header>

<section class="hero">
  <div class="hero-photo" role="img" aria-label="Photo of a smiling finance adviser working at a laptop with a colleague in a bright office"></div>
  <div class="hero-kicker">Brightpath Finance</div>
  <h1 class="hero-title">Debt Consolidation</h1>
  <p class="hero-copy">Lorem ipsum dolor sit amet, consectetur adipiscing elit, sed do eiusmod tempor incididunt ut labore et dolor sit amet, consectetur</p>
  <div class="btn-read">Read More</div>
  <div class="slide-arrow" style="left:30px"><svg width="12" height="14" viewBox="0 0 12 14"><path d="M9 1 3 7l6 6" stroke="#fff" stroke-width="2" fill="none"/></svg></div>
  <div class="slide-arrow" style="left:1131px"><svg width="12" height="14" viewBox="0 0 12 14"><path d="m3 1 6 6-6 6" stroke="#fff" stroke-width="2" fill="none"/></svg></div>

  <form class="apply-panel">
    <h2>Get Started Today!</h2>
    <div class="field" style="top:74px">First Name :</div>
    <div class="field" style="top:117px">Email :</div>
    <div class="field" style="top:160px">Phone :</div>
    <div class="field field-select" style="top:203px">State :</div>
    <div class="field" style="top:246px">Loan amount :</div>
    <div class="btn-signup">Sign Up Now</div>
    <div class="rates">
      <h3>The Interest Rates of the Month</h3>
      <div class="rate-row"><span>Credit Loans</span><span>3.02%</span></div>
      <div class="rate-row"><span>Credit Car Loans</span><span>30%</span></div>
      <div class="rate-row"><span>Credit Truck Loans</span><span>2.05%</span></div>
    </div>
  </form>
</section>

<section class="services">
  <h2 class="section-title" style="top:58px">Our Services</h2>
  <div class="title-rule" style="top:106px"></div>

  <article class="service-card" style="left:99px">
    <div class="service-head">Bas Agent</div>
    <div class="service-photo" role="img" aria-label="Photo of an agent handing keys to a smiling couple" style="background:linear-gradient(135deg,#dfe4ea,#9aa6b2)"></div>
    <p class="service-text">Lorem ipsum dolor sit amet, consectt adipiscing elit, sed do eiusmod tepor incididunt ut labore et dolore</p>
    <div class="btn-click">Click Here <svg width="10" height="10" viewBox="0 0 10 10"><circle cx="5" cy="5" r="5" fill="#333"/><path d="m4 3 2 2-2 2" stroke="#fff" fill="none"/></svg></div>
  </article>
  <article class="service-card" style="left:353px">
    <div class="service-head">Payroll &amp; Bookkeeping</div>
    <div class="service-photo" role="img" aria-label="Photo of a woman signing paperwork at a desk" style="background:linear-gradient(135deg,#e9e2d8,#8a8f98)"></div>
    <p class="service-text">Lorem ipsum dolor sit amet, consectt adipiscing elit, sed do eiusmod tepor incididunt ut labore et dolore</p>
    <div class="btn-click">Click Here <svg width="10" height="10" viewBox="0 0 10 10"><circle cx="5" cy="5" r="5" fill="#333"/><path d="m4 3 2 2-2 2" stroke="#fff" fill="none"/></svg></div>
  </article>
  <article class="service-card" style="left:607px">
    <div class="service-head">Credit File Repair</div>
    <div class="service-photo" role="img" aria-label="Photo of a mechanic repairing a car in a workshop" style="background:linear-gradient(135deg,#6b7380,#2e3440)"></div>
    <p class="service-text">Lorem ipsum dolor sit amet, consectt adipiscing elit, sed do eiusmod tepor incididunt ut labore et dolore</p>
    <div class="btn-click">Click Here <svg width="10" height="10" viewBox="0 0 10 10"><circle cx="5" cy="5" r="5" fill="#333"/><path d="m4 3 2 2-2 2" stroke="#fff" fill="none"/></svg></div>
  </article>
  <article class="service-card" style="left:861px">
    <div class="service-head">Debt Consolidation</div>
    <div class="service-photo" role="img" aria-label="Photo of a hand with a pen over financial charts" style="background:linear-gradient(135deg,#f0ebe4,#b9a89a)"></div>
    <p class="service-text">Lorem ipsum dolor sit amet, consectt adipiscing elit, sed do eiusmod tepor incididunt ut labore et dolore</p>
    <div class="btn-click">Click Here <svg width="10" height="10" viewBox="0 0 10 10"><circle cx="5" cy="5" r="5" fill="#333"/><path d="m4 3 2 2-2 2" stroke="#fff" fill="none"/></svg></div>
  </article>
</section>

<section class="steps">
  <div class="steps-photo" role="img" aria-label="Faded blue photo of a laptop and coffee cup on a desk"></div>
  <h2 class="section-title" style="top:66px">3 Steps for Fast Finance</h2>

  <div class="step-circle" style="left:212px">
    <svg width="42" height="42" viewBox="0 0 24 24" fill="none" stroke="#0255a3" stroke-width="1.8"><path d="M11 4H5a1 1 0 0 0-1 1v14a1 1 0 0 0 1 1h14a1 1 0 0 0 1-1v-6"/><path d="M18 3l3 3-9 9H9v-3z"/></svg>
  </div>
  <div class="step-circle" style="left:563px">
    <svg width="42" height="42" viewBox="0 0 24 24" fill="none" stroke="#0255a3" stroke-width="1.8" stroke-linejoin="round"><path d="M22 2 2 10l7 3 3 7z"/><path d="M22 2 9 13"/></svg>
  </div>
  <div class="step-circle" style="left:915px;font-size:42px;color:var(--blue);font-weight:500">$</div>

  <svg class="abs" style="left:390px;top:195px" width="80" height="40" viewBox="0 0 80 40"><path d="M4 26 Q40 2 72 26" stroke="#fff" stroke-width="3" fill="none"/><path d="m64 20 10 8-12 2" stroke="#fff" stroke-width="3" fill="none"/></svg>
  <svg class="abs" style="left:752px;top:215px" width="80" height="40" viewBox="0 0 80 40"><path d="M4 30 Q40 40 72 10" stroke="#fff" stroke-width="3" fill="none"/><path d="m62 8 12 0-2 12" stroke="#fff" stroke-width="3" fill="none"/></svg>

  <div class="step-title" style="left:76px">Apply Online in Minutes</div>
  <div class="step-title" style="left:427px">Fast Approval Process</div>
  <div class="step-title" style="left:779px">Get Finance Fast</div>
  <p class="step-text" style="left:131px">Nemo enim ipsam voluptatem quia voluptas sit aspernatur aut odit aut fugit, sed quia consntur magni dolores eos qui ratione</p>
  <p class="step-text" style="left:482px">Nemo enim ipsam voluptatem quia voluptas sit aspernatur aut odit aut fugit, sed quia consntur magni dolores eos qui ratione</p>
  <p class="step-text" style="left:834px">Nemo enim ipsam voluptatem quia voluptas sit aspernatur aut odit aut fugit, sed quia consntur magni dolores eos qui ratione</p>
  <div class="btn-apply-steps">Apply Now</div>
</section>

<section class="reviews">
  <h2 class="section-title" style="top:60px;font-size:26px">Customer Reviews</h2>

  <div class="review" style="left:130px">
    <p class="review-text">Lorem ipsum dolor sit amet, consectetur adipisicing elit, sed do eiusmod tempor incididunt ut labore et dolore magna aliqua Unde omnis, consequuntur.</p>
    <div class="reviewer" style="left:26px">
      <div class="avatar" role="img" aria-label="Customer portrait photo"></div>
      <div><div class="reviewer-name">John Doe - Clearway Lending</div>
        <div class="stars"><span></span><span></span><span></span><span></span><span></span></div></div>
    </div>
  </div>
  <div class="review" style="left:652px">
    <p class="review-text">Lorem ipsum dolor sit amet, consectetur adipisicing elit, sed do eiusmod tempor incididunt ut labore et dolore magna aliqua Unde omnis, consequuntur.</p>
    <div class="reviewer" style="left:26px">
      <div class="avatar" role="img" aria-label="Customer portrait photo" style="background:radial-gradient(circle at 50% 40%,#b89880,#5e4a3c)"></div>
      <div><div class="reviewer-name">John Doe - Clearway Lending</div>
        <div class="stars"><span></span><span></span><span></span><span></span><span></span></div></div>
    </div>
  </div>
</section>

<section class="partners" aria-label="Partner lenders">
  <div class="partner" style="left:137px;width:64px"></div>
  <div class="partner" style="left:258px;width:114px"></div>
  <div class="partner" style="left:431px;width:94px"></div>
  <div class="partner" style="left:594px;width:110px"></div>
  <div class="partner" style="left:787px;width:82px"></div>
  <div class="partner" style="left:942px;width:116px"></div>
</section>

<footer class="site-footer">
  <div class="foot-brand"><span class="brand-dot"></span><span class="brand-name" style="font-size:20px">Brightpath Finance</span></div>

  <div class="foot-col"><h4 style="left:276px">Contacts Us</h4></div>
  <div class="contact-line" style="top:72px">
    <svg width="12" height="16" viewBox="0 0 12 16"><path d="M6 0a6 6 0 0 0-6 6c0 4.5 6 10 6 10s6-5.5 6-10a6 6 0 0 0-6-6zm0 8.5A2.5 2.5 0 1 1 6 3.5a2.5 2.5 0 0 1 0 5z" fill="#6aa3d6"/></svg>
    <span>Brightpath Finance P.O. Box 4821 Harbour City,<br>Australia</span></div>
  <div class="contact-line" style="top:127px">
    <svg width="14" height="14" viewBox="0 0 24 24"><path fill="#6aa3d6" d="M6.6 10.8a15.1 15.1 0 0 0 6.6 6.6l2.2-2.2c.3-.3.7-.4 1-.2 1.1.4 2.3.6 3.6.6.6 0 1 .4 1 1V20c0 .6-.4 1-1 1A17 17 0 0 1 3 4c0-.6.4-1 1-1h3.5c.6 0 1 .4 1 1 0 1.3.2 2.5.6 3.6.1.3 0 .7-.2 1z"/></svg>
    <span>Phone: +1300 555 017</span></div>
  <div class="contact-line" style="top:158px">
    <svg width="14" height="12" viewBox="0 0 14 12"><rect width="14" height="12" rx="1" fill="#6aa3d6"/><path d="m1 2 6 4 6-4" stroke="#fff" fill="none"/></svg>
    <span>info@brightpathfinance.example.com.au</span></div>

  <div class="foot-col"><h4 style="left:624px">Sign Up for Newsletter</h4></div>
  <p class="newsletter-copy">Get the latest updates on our courses and events: Notify Me</p>
  <div class="news-input" style="top:118px">Enter Name</div>
  <div class="news-input" style="top:167px;width:165px">Enter Email</div>
  <div class="btn-subscribe">Subscribe</div>

  <div class="foot-col"><h4 style="left:970px">Information</h4></div>
  <ul class="info-links">
    <li>Bas Agent</li>
    <li>Payroll And Bookkeeping</li>
    <li>Credit File Repair</li>
    <li>Default Removals</li>
    <li>Debt Consolidation</li>
  </ul>
</footer>

<div class="footer-bar">©2015 - 2016 Brightpath Finance .. All Rights Reserved.</div>

</body>
</html>
```